Q.B. Brightpath Store

The design is for eCommerce home page but I would like it to complement this site: http://www.qbbrightpathsolutions.com/ but... it should also have independence as a standalone site.

The best design will be able to effectively mix corporate with a high quality small business consumer feel. It should be completely custom design, not a template look or feel. I want the users to get the feeling that this is the place to go for buying tech for business. We sell the same products as RVK.

You can be creative as you wish, as long as the elements of a great eCommerce site are present.

I would like your 'design' to blow these away:
http://www.shopping.zl.com/
mirabelo.com
http://www.rvk.com/

Here are references:
Call to action
http://markvantage.com/us/blog/48153-seven-tips-for-designing-an-effective-ecommerce-call-to-action

Effective Ecommerce design
http://www.vexa.com/ss/7-tips-for-effective-e-commerce#0

91 points of ecommerce
http://qir.com/blog/holygrail-of-ecommerce-conversion-optimization-91-points-checklist

UPDATE 07/11/2013:

Please look at the category sample png files. I see already many people are using the main menu from qbbrightpathsolutions.com and I do not mind your creativiety, but this is an eCommerce store and people need a menu to get to the categories and/or product types. I don't want to limit anyone creativity by the png samples. I'm also not using them to show I like them in any particular way or form, just that it's needed, whether it's a button (dropdown of course) that says 'Categories' or 'Products, whether it an accordion, horizontal or vertical.

Thanks

UPDATE 07/12/2013:

Please find other use of space that has been used for About Us paragraph (if you've added it to the page). About Us should have it's own page and the purpose of the design should be to sell products (and some services as products). Please put a link or some other creative method to lead users to the About Us page.

Reason: I've raised the award, including 1st, 2nd, and 3rd place and participation payments so I will also extend 7 days. Thanks!

I've updated the product brief. Please scroll down to where it says: UPDATE 07/11/2013

Thanks!

UPDATE 07/12/2013:

Please find other use of space that has been used for About Us paragraph (if you've added it to the page).  About Us should have it's own page and the purpose of the design should be to sell products (and some services as products). Please put a link or some other creative method to lead users to the About Us page if you must but not on the real estate of the page.

Thanks!

Added updates to the brief 7/14/2013.

Thanks!

The voting is in and the project is complete.  Thanks everyone for joining, all of those who participated are truly amazingly talented. But, there were only 3 prizes.  I will be having further projects down the line to develop other pages to this site after the initial implementation is completed.  I truly would like to have you all back. 

- Thank you.

Target Market(s)

corporate decision-makers AND small business consumers

Industry/Entity Type

Small Business

Requirements
Must have
• Call to action.
Openness (non-clutter).

These elements:
Search box
Logo
Tagline
Telephone number
Contact details
Address
My account / sign in
Shopping basket / checkout link
Latest offers
Promotional area
Email sign up
Delivery information
About us
Link to press office / corporate site
Terms and conditions
Sitemap for the footer.
Delivery offers: free
Personalized recommendations
Social media links
Accepted payment methods
Link to blog or community section
Change language / country

http://smartplansblog.pelloware.com/sales-leads-landing-page/

UPDATE 07/14/2013
Category Menu. This can be a dropdown, horizontal, vertical, etc. But shoppers need to know how to get to the products they want to buy.
Nice to have
• Trustmarks
Blog/Blog link

UPDATE 07/12/2013:
Make the footer useful.

UPDATE 07/14/2013 (Suggestions of elements to differentiate your designs)

-Quick Shop: A quick buy module/section: Where a user can put in a SKU number or Model number to quickly add the product to their shopping cart.

-Featured
-Best Sellers
-Specials
-Trending Tags/Tag Cloud
- Activity Stream
- Cross Sell/ Up Sell
- Testimonial
- Social Network Feed
- Live Help
- Feedback/Support/Contact Tab
- Show logged in user (i.e. Welcome, Mark Pelley)
Should not have
• The design SHOULD NOT be generic like this:

http://www.artgatherly.com/design/52392
http://www.falconmart.com/

The page should not feel over cluttered. It should not have low quality icons or design elements. Navigation should not be hard to discover or confusing.

```html
<!DOCTYPE html>
<html lang="en">
<head>
<meta charset="utf-8">
<title>Q.B. Brightpath Store</title>
<link rel="stylesheet" href="https://fonts.googleapis.com/css2?family=Mulish:wght@300;400;600;700;800;900&display=swap">
<style>
:root{
  --blue:#0a63a8;
  --blue-deep:#05468a;
  --blue-link:#1a72c0;
  --blue-light:#2d8fd8;
  --navy:#0b2c5c;
  --ink:#444;
  --muted:#666;
  --topbar:#f4f4f4;
  --line:#dcdcdc;
  --footer:#4a4a4a;
  --footer-dark:#3b3b3b;
  --footer-text:#cfcfcf;
  --white:#fff;
}
*{box-sizing:border-box;margin:0;padding:0}
html,body{width:1162px;height:1200px;overflow:hidden}
body{font-family:"Mulish",Arial,sans-serif;color:var(--ink);background:var(--white);position:relative}
a{color:inherit;text-decoration:none}
.wrap{position:absolute;left:194px;width:776px}

/* top bar */
.topbar{position:absolute;top:0;left:0;width:100%;height:40px;background:linear-gradient(#fafafa,#eeeeee);border-bottom:1px solid var(--line)}
.topbar .wrap{top:0;height:40px;display:flex;align-items:center;justify-content:space-between}
.topbar nav{display:flex;gap:22px;font-size:11px;color:var(--ink)}
.account{font-size:12px;color:var(--ink)}
.account a{color:var(--blue-link)}

/* header */
.header{position:absolute;top:40px;left:0;width:100%;height:66px;border-bottom:1px solid var(--line)}
.brand{position:absolute;left:194px;top:14px;display:flex;align-items:center;gap:8px}
.brand-mark{width:38px;height:38px;border-radius:50%;background:var(--blue)}
.brand-name{font-size:16px;font-weight:800;color:var(--blue);line-height:1.1;width:100px}
.main-nav{position:absolute;left:398px;top:17px;display:flex;gap:34px}
.main-nav a{display:block}
.main-nav strong{display:block;font-size:18px;font-weight:800;color:var(--blue-link);letter-spacing:-.3px;line-height:1}
.main-nav span{display:block;font-size:12px;color:var(--muted);margin-top:3px}
.cart{position:absolute;left:872px;top:19px;width:98px;height:30px;background:linear-gradient(#1a6cb6,#0a4f97);color:var(--white);font-weight:800;font-size:18px;display:flex;align-items:center;justify-content:center;gap:6px}

/* search row */
.searchrow{position:absolute;top:106px;left:0;width:100%;height:45px;background:#f1f1f1;border-bottom:1px solid var(--line)}
.search-input{position:absolute;left:194px;top:8px;width:299px;height:29px;background:var(--white);border:1px solid #d4d4d4;font-size:14px;color:#c8c8c8;padding:6px 12px;letter-spacing:.5px}
.search-btn{position:absolute;left:497px;top:8px;width:84px;height:28px;background:linear-gradient(#1468b3,#0a4a8f);display:flex;align-items:center;justify-content:center}
.phone{position:absolute;left:626px;top:8px;font-size:24px;font-weight:800;color:#444;display:flex;align-items:center;gap:6px}
.social{position:absolute;left:864px;top:10px;display:flex;gap:3px}
.social span{width:24px;height:24px;border-radius:50%;background:var(--blue-deep)}

/* hero */
.hero{position:absolute;top:151px;left:0;width:100%;height:291px;background:linear-gradient(180deg,#f6f6f6,#ffffff 60%)}
.hero-art{position:absolute;left:194px;top:8px;width:380px;height:283px;border-radius:50% 50% 0 0;background:radial-gradient(circle at 45% 45%,#e9ecf2 0,#a9bde4 40%,#6d8fd4 60%,rgba(255,255,255,0) 72%)}
.hero-copy{position:absolute;left:592px;top:100px}
.hero-copy .kicker{font-size:24px;font-weight:400;color:var(--blue-light);letter-spacing:-.4px;line-height:1}
.hero-copy h1{font-size:30px;font-weight:900;color:var(--navy);letter-spacing:-1px;line-height:1.05}
.learn{display:inline-flex;align-items:center;gap:4px;font-size:17px;color:#555;margin-top:20px;letter-spacing:.3px}
.pager{position:absolute;display:flex;gap:3px}
.pager span{width:16px;height:19px;background:var(--blue);display:flex;align-items:center;justify-content:center}

/* welcome band */
.band{position:absolute;top:442px;left:0;width:100%;height:172px;background:var(--blue)}
.welcome{position:absolute;left:194px;top:20px;width:380px;color:var(--white)}
.welcome h2{font-size:30px;font-weight:800;letter-spacing:-.8px;line-height:1}
.welcome p{font-size:12px;line-height:1.25;margin-top:9px}
.welcome .learn{color:var(--white);font-size:14px;margin-top:8px}
.promo{position:absolute;left:592px;top:17px;width:378px;height:138px;background:var(--white)}
.promo-art{position:absolute;left:16px;top:18px;width:150px;height:108px;background:linear-gradient(135deg,#d7e7f6,#7fb2e2 55%,#4a4f5c);border-radius:6px}
.promo-copy{position:absolute;left:174px;top:38px}
.promo-copy h3{font-size:29px;font-weight:900;color:var(--navy);letter-spacing:-1px;line-height:1}
.promo-copy p{font-size:14px;font-weight:700;color:var(--blue-link);letter-spacing:-.3px;margin-top:3px}
.promo-copy .learn{font-size:14px;margin-top:10px}

/* offers */
.offers{position:absolute;top:614px;left:194px;width:776px}
.offers h2{position:absolute;top:24px;font-size:26px;font-weight:900;color:var(--blue-deep);letter-spacing:-1px}
.cards{position:absolute;top:63px;display:flex;gap:14px}
.card{width:183px;height:182px;background:var(--white);box-shadow:0 0 3px rgba(0,0,0,.18);position:relative}
.card h3{font-size:14.5px;font-weight:800;color:var(--blue-link);letter-spacing:-.6px;text-align:center;margin-top:14px;white-space:nowrap}
.card-art{position:absolute;left:22px;right:22px;top:40px;height:128px;border-radius:8px}

/* newsletter */
.news{position:absolute;top:885px;left:0;width:100%;height:57px;background:linear-gradient(90deg,var(--blue) 0,var(--blue) 582px,var(--blue-deep) 582px)}
.news-label{position:absolute;left:192px;top:17px;font-size:17px;font-weight:800;color:var(--white);letter-spacing:-.6px}
.news-form{position:absolute;left:288px;top:14px;width:280px;height:30px;background:var(--white);display:flex;align-items:center;padding:3px}
.news-form span{flex:1;font-size:14px;color:#c8c8c8;padding-left:6px;letter-spacing:.4px}
.news-form strong{width:102px;height:24px;background:var(--blue-deep);color:var(--white);font-size:17px;font-weight:800;display:flex;align-items:center;justify-content:center;letter-spacing:-.4px}
.delivery{position:absolute;left:596px;top:15px;font-size:24px;font-weight:900;color:var(--white);letter-spacing:-1px}
.delivery em{font-style:normal;color:var(--blue-light)}

/* footer */
.footer{position:absolute;top:942px;left:0;width:100%;height:202px;background:var(--footer)}
.footer .brand{top:18px}
.footer .brand-mark{background:#888}
.footer .brand-name{color:#bdbdbd}
.accept{position:absolute;left:194px;top:84px}
.accept h4{font-size:15px;font-weight:800;color:#ddd}
.cards-accepted{display:flex;gap:4px;margin-top:6px}
.cards-accepted span{height:17px;border-radius:2px}
.col{position:absolute;top:20px}
.col h4{font-size:14.5px;font-weight:800;color:#ddd;text-transform:uppercase;letter-spacing:.2px;white-space:nowrap}
.col ul{list-style:none;margin-top:7px}
.col li{font-size:11.5px;color:var(--footer-text);line-height:20px;white-space:nowrap}
.copyright{position:absolute;left:197px;top:176px;font-size:11.5px;color:#b8b8b8}
.bottombar{position:absolute;top:1144px;left:0;width:100%;height:56px;background:var(--footer-dark);display:flex;align-items:center}
.bottombar .inner{position:absolute;left:197px;display:flex;align-items:center;gap:18px;color:var(--white);font-size:11.5px}
.bottombar h4{font-size:15px;font-weight:800;letter-spacing:.2px;margin-right:2px}
.bottombar .item{display:flex;align-items:center;gap:6px}
</style>
</head>
<body>

<header class="topbar">
  <div class="wrap">
    <nav>
      <a href="#">Home</a><a href="#">Small Business</a><a href="#">Enterprise</a><a href="#">Non-Profit</a><a href="#">Billing</a><a href="#">Get Support</a><a href="#">Contact Us</a>
    </nav>
    <div class="account"><a href="#">Sign In</a> or <a href="#">Register</a></div>
  </div>
</header>

<div class="header">
  <a class="brand" href="#"><span class="brand-mark"></span><span class="brand-name">Q.B. Brightpath Store</span></a>
  <nav class="main-nav">
    <a href="#"><strong>Hardware</strong><span>Fulfillment</span></a>
    <a href="#"><strong>Software</strong><span>Licensing</span></a>
    <a href="#"><strong>IT Resource</strong><span>Management</span></a>
    <a href="#"><strong>Technology</strong><span>Services</span></a>
  </nav>
  <a class="cart" href="#">
    <svg width="20" height="16" viewBox="0 0 20 16" fill="none" stroke="#fff" stroke-width="1.6"><path d="M1 1h3l2 9h10l2-7H5"/><circle cx="8" cy="14" r="1.3" fill="#fff"/><circle cx="15" cy="14" r="1.3" fill="#fff"/></svg>
    Cart
    <svg width="12" height="8" viewBox="0 0 12 8" fill="none" stroke="#fff" stroke-width="1.5"><path d="M1 1l5 5 5-5"/></svg>
  </a>
</div>

<div class="searchrow">
  <div class="search-input">Search</div>
  <div class="search-btn"><svg width="18" height="18" viewBox="0 0 18 18" fill="none" stroke="#fff" stroke-width="2"><circle cx="7" cy="7" r="5.5"/><path d="M11 11l6 6"/></svg></div>
  <div class="phone"><svg width="16" height="18" viewBox="0 0 16 18"><path d="M3 1l3 0 1 4-2 2c1 2 3 4 5 5l2-2 4 1v3c0 1-1 2-2 2C7 16 1 10 1 3c0-1 1-2 2-2z" fill="#1a72c0"/></svg>888 555 0142</div>
  <div class="social"><span></span><span></span><span></span><span></span></div>
</div>

<section class="hero">
  <div class="hero-art" role="img" aria-label="Illustration of white and blue cubes assembling into a larger cube"></div>
  <div class="hero-copy">
    <p class="kicker">technology solutions &amp; services</p>
    <h1>that exceeds desired results</h1>
    <a class="learn" href="#"><svg width="20" height="12" viewBox="0 0 20 12" fill="none" stroke="#666" stroke-width="1.5"><path d="M2 1l5 5-5 5M9 1l5 5-5 5"/></svg>LEARN MORE</a>
  </div>
  <div class="pager" style="left:936px;top:259px">
    <span><svg width="8" height="12" viewBox="0 0 8 12" fill="none" stroke="#fff" stroke-width="1.6"><path d="M7 1L2 6l5 5"/></svg></span>
    <span><svg width="8" height="12" viewBox="0 0 8 12" fill="none" stroke="#fff" stroke-width="1.6"><path d="M1 1l5 5-5 5"/></svg></span>
  </div>
</section>

<section class="band">
  <div class="welcome">
    <h2>welcome</h2>
    <p>Vivamus lacus neque, euismod vitae elementum sed, rutrum a turpis. Suspendisse fringilla quam a eleifend aliquet. Nulla facilisi. Praesent quam arcu, scelerisque eget luctus ac, dignissim eget ipsum. Praesent varius nibh ac nulla aliquam convallis. Ut tincidunt luctus nisi vitae malesuada.</p>
    <a class="learn" href="#"><svg width="18" height="12" viewBox="0 0 20 12" fill="none" stroke="#fff" stroke-width="1.5"><path d="M2 1l5 5-5 5M9 1l5 5-5 5"/></svg>LEARN MORE</a>
  </div>
  <div class="promo">
    <div class="promo-art" role="img" aria-label="Laptop, phone and tablets connected to a cloud"></div>
    <div class="promo-copy">
      <h3>GET 20% OFF</h3>
      <p>at all cloud storage services</p>
      <a class="learn" href="#"><svg width="18" height="12" viewBox="0 0 20 12" fill="none" stroke="#666" stroke-width="1.5"><path d="M2 1l5 5-5 5M9 1l5 5-5 5"/></svg>LEARN MORE</a>
    </div>
    <div class="pager" style="left:344px;top:117px">
      <span><svg width="8" height="12" viewBox="0 0 8 12" fill="none" stroke="#fff" stroke-width="1.6"><path d="M7 1L2 6l5 5"/></svg></span>
      <span><svg width="8" height="12" viewBox="0 0 8 12" fill="none" stroke="#fff" stroke-width="1.6"><path d="M1 1l5 5-5 5"/></svg></span>
    </div>
  </div>
</section>

<section class="offers">
  <h2>Latest Offers</h2>
  <div class="cards">
    <article class="card"><h3>Personal 3D Viewer</h3><div class="card-art" role="img" aria-label="White head-mounted 3D viewer" style="background:radial-gradient(circle,#ffffff 20%,#cfd3d8 55%,#2a2a2a 80%,#fff 82%)"></div></article>
    <article class="card"><h3>Novara S Series 15 Laptop</h3><div class="card-art" role="img" aria-label="White laptop with colourful tiled start screen" style="background:linear-gradient(180deg,#2b2f6a 0,#3b5aa0 55%,#e6e6e6 75%,#fafafa)"></div></article>
    <article class="card"><h3>XGA 3LCD Mobile Projector</h3><div class="card-art" role="img" aria-label="White compact projector" style="background:linear-gradient(160deg,#ffffff 20%,#e2e4e7 60%,#9aa0a8)"></div></article>
    <article class="card"><h3>Smart Wireless Headset Pro</h3><div class="card-art" role="img" aria-label="Black wireless headset clip with earbud cables" style="background:radial-gradient(ellipse at 50% 55%,#2a2a2a 0,#5a5a5a 22%,#ffffff 45%)"></div></article>
  </div>
</section>

<section class="news">
  <div class="news-label">Newsletter</div>
  <div class="news-form"><span>Email Address</span><strong>Subscribe</strong></div>
  <div class="delivery">FREE <em>DELIVERY OVER</em> $90 <em>SALES</em></div>
</section>

<footer class="footer">
  <a class="brand" href="#"><span class="brand-mark"></span><span class="brand-name">Q.B. Brightpath Store</span></a>
  <div class="accept">
    <h4>We Accept</h4>
    <div class="cards-accepted">
      <span style="width:58px;background:#e8edf5"></span>
      <span style="width:26px;background:#f2f2f2"></span>
      <span style="width:26px;background:#e98b2a"></span>
      <span style="width:17px;background:#3b8fd8"></span>
    </div>
  </div>
  <div class="col" style="left:375px"><h4>Our Company</h4><ul><li>About Us</li><li>Careers</li><li>Corporate</li><li>Partners</li><li>Get Support</li><li>Contact Us</li></ul></div>
  <div class="col" style="left:514px"><h4>Quick Links</h4><ul><li>Home</li><li>Small Business</li><li>Enterprise</li><li>Non-Profit</li><li>Billing</li><li>Go Shopping</li></ul></div>
  <div class="col" style="left:635px"><h4>Our Websites</h4><ul><li>qbbrightpathstore.com</li><li>qbbrightpathinc.com</li><li>qbbrightpathsupport.com</li><li>qbbrightpatheducation</li></ul></div>
  <div class="col" style="left:777px"><h4>Products and Services</h4><ul><li>Hardware Fulfillment</li><li>Software Licensing</li><li>Resource Management</li><li>Technical Services</li><li>Exchange Board</li><li>Partner Program</li><li>Recycle</li></ul></div>
  <p class="copyright">Copyright © 2013 Q.B. Brightpath Store.</p>
</footer>

<div class="bottombar">
  <div class="inner">
    <h4>GET IN TOUCH TODAY</h4>
    <span class="item"><svg width="15" height="15" viewBox="0 0 16 16" fill="none" stroke="#fff" stroke-width="1.5"><circle cx="8" cy="8" r="6.5"/><path d="M11 5L7 7 5 11l4-2z" fill="#fff"/></svg>42 Larkmoor Road, Suite # 118 Elmsford, NY 10599</span>
    <span class="item"><svg width="14" height="15" viewBox="0 0 16 18"><path d="M3 1l3 0 1 4-2 2c1 2 3 4 5 5l2-2 4 1v3c0 1-1 2-2 2C7 16 1 10 1 3c0-1 1-2 2-2z" fill="#fff"/></svg>+1 (888) 555 0199</span>
    <span class="item"><svg width="16" height="12" viewBox="0 0 16 12" fill="none" stroke="#fff" stroke-width="1.3"><rect x="1" y="1" width="14" height="10"/><path d="M1 1l7 6 7-6"/></svg>info@qbbrightpathinc.com</span>
  </div>
</div>

</body>
</html>
```